To design a brand identity that is simple and creative with 'Corvane' as the brand name, I like modern simple fonts like helvetica neue, I want to print both sides of the card, I am open to dark front and white back, but the design needs to transfer well to letter heads and email signatures, I am looking for sophisticated and elegant, but open minded about clever and off the wall, I do not do 'boring' Corvane Ventures is the mother company for a small group, specialising in Management & consulting, Software development and construction, we have a high level of integrity, we are transparent and accountable for what we do. my images are provided as a guide only, Im not expecting them to be just copied, Im looking for a creator and passionate thinker, who will put life into their work.

Target Market(s)

usually business minded people who are looking for something different in me, such as leadership, confidence and focus with thinking that is per haps a little outside the box..

Industry/Entity Type

Construction

Requirements
Must have
• clean, minmalistic
Nice to have
• custom logo
Should not have
• boring, traditional

```html
<!DOCTYPE html>
<html lang="en">
<head>
<meta charset="utf-8">
<title>Corvane Ventures – Business Card</title>
<link href="https://fonts.googleapis.com/css2?family=Open+Sans:wght@300;400;700&family=Cormorant+Garamond:ital,wght@1,400&display=swap" rel="stylesheet">
<style>
  :root {
    --stage: #ecebe8;
    --card-dark: #1d1d1f;
    --card-dark-edge: #2a2a2d;
    --card-light: #ffffff;
    --brand-orange: #f0642a;
    --tagline-grey: #8a8a8a;
    --band-orange: #f7a21b;
    --band-red: #e8192c;
    --band-magenta: #a2306f;
    --band-teal: #12a08f;
    --contact-text: #e6e6e6;
    --icon-yellow: #f2c21a;
    --divider: #8d8d8d;
    --url-text: #2b2b2b;
    --pastel-mark: #f6dede;
  }
  * { box-sizing: border-box; margin: 0; padding: 0; }
  html, body {
    width: 1200px; height: 720px; overflow: hidden;
    background: var(--stage);
  }
  .canvas {
    width: 1200px; height: 720px;
    display: flex; align-items: center; justify-content: center; gap: 40px;
  }
  .card {
    position: relative;
    width: 540px; height: 309px;
    border-radius: 4px;
    overflow: hidden;
    box-shadow: 0 6px 18px rgba(0,0,0,0.18);
  }

  /* Front */
  .card--front {
    background: linear-gradient(160deg, var(--card-dark-edge), var(--card-dark) 60%);
  }
  .front-texture {
    position: absolute; inset: 0;
    background: linear-gradient(180deg, rgba(255,255,255,0.04), rgba(0,0,0,0.15));
  }
  .brand-lockup {
    position: absolute; left: 40px; top: 46px;
    display: flex; align-items: center; gap: 18px;
  }
  .brand-dot {
    width: 50px; height: 50px; border-radius: 50%;
    background: var(--brand-orange);
  }
  .brand-name {
    font-family: "Open Sans", Arial, sans-serif;
    font-weight: 300;
    font-size: 66px;
    line-height: 1;
    letter-spacing: 1px;
    color: var(--brand-orange);
  }
  .tagline {
    position: absolute; left: 210px; top: 124px;
    font-family: "Cormorant Garamond", Georgia, serif;
    font-style: italic;
    font-size: 17px;
    color: var(--tagline-grey);
  }
  .rule {
    position: absolute; left: 0; right: 0; height: 1px;
    background: rgba(255,255,255,0.18);
  }
  .rule--top { top: 160px; }
  .rule--bottom { top: 216px; }
  .name-band {
    position: absolute; left: 0; right: 0; top: 166px; height: 44px;
    display: flex; align-items: center; justify-content: center;
    background: linear-gradient(90deg, var(--band-orange) 0%, var(--band-red) 38%, var(--band-magenta) 72%, var(--band-teal) 100%);
  }
  .name-band__text {
    font-family: "Open Sans", Arial, sans-serif;
    font-size: 17px; font-weight: 400;
    color: #fff;
  }
  .name-band__text strong { font-weight: 700; }
  .contact {
    position: absolute; left: 0; right: 0; top: 234px;
    display: flex; justify-content: center; align-items: center; gap: 18px;
    font-family: "Open Sans", Arial, sans-serif;
    font-size: 13px; line-height: 22px;
    color: var(--contact-text);
  }
  .contact__address { text-align: right; }
  .contact__divider { width: 1px; height: 46px; background: var(--divider); }
  .contact__line { display: flex; align-items: center; gap: 7px; }
  .contact__icon { width: 13px; height: 13px; flex: none; }

  /* Back */
  .card--back { background: var(--card-light); }
  .back-mark {
    position: absolute; left: 175px; top: 40px;
    width: 190px; height: 190px; border-radius: 50%;
    background: var(--pastel-mark);
    opacity: 0.7;
  }
  .back-name {
    position: absolute; left: 0; right: 0; top: 78px;
    text-align: center;
    font-family: "Open Sans", Arial, sans-serif;
    font-weight: 300;
    font-size: 100px;
    line-height: 1;
    color: var(--brand-orange);
  }
  .back-url {
    position: absolute; left: 0; right: 0; top: 246px;
    text-align: center;
    font-family: "Open Sans", Arial, sans-serif;
    font-size: 17px;
    letter-spacing: 4px;
    color: var(--url-text);
  }
</style>
</head>
<body>
<main class="canvas">

  <section class="card card--front" aria-label="Business card front">
    <div class="front-texture" role="img" aria-label="Dark woven carbon texture background"></div>
    <div class="brand-lockup">
      <div class="brand-dot"></div>
      <div class="brand-name">corvane</div>
    </div>
    <p class="tagline">…in the creation business.</p>
    <div class="rule rule--top"></div>
    <div class="name-band">
      <p class="name-band__text"><strong>Your Name,</strong> Title</p>
    </div>
    <div class="rule rule--bottom"></div>
    <div class="contact">
      <div class="contact__address">Po Box 512<br>Parth 6031</div>
      <div class="contact__divider"></div>
      <div class="contact__details">
        <div class="contact__line">
          <svg class="contact__icon" viewBox="0 0 16 16" aria-hidden="true">
            <circle cx="8" cy="8" r="8" fill="var(--icon-yellow)"/>
            <path d="M5.2 4.2l1.5-.4 1 2.2-1 .8a6 6 0 0 0 2.5 2.5l.8-1 2.2 1-.4 1.5c-3.4.3-6.9-3.2-6.6-6.6z" fill="#1d1d1f"/>
          </svg>
          <span>+61 0400 555 214</span>
        </div>
        <div class="contact__line">
          <svg class="contact__icon" viewBox="0 0 16 16" aria-hidden="true">
            <circle cx="8" cy="8" r="8" fill="var(--icon-yellow)"/>
            <rect x="3.5" y="5" width="9" height="6" rx="0.8" fill="#1d1d1f"/>
            <path d="M3.8 5.4L8 8.6l4.2-3.2" fill="none" stroke="var(--icon-yellow)" stroke-width="0.9"/>
          </svg>
          <span>names@corvane.ventures</span>
        </div>
      </div>
    </div>
  </section>

  <section class="card card--back" aria-label="Business card back">
    <div class="back-mark"></div>
    <div class="back-name">corvane</div>
    <p class="back-url">www.corvane.com</p>
  </section>

</main>
</body>
</html>
```